TLR Handyman Service

File 2 Prep kitchen cabinets
File 3 Painting kitchen cabinets
File 4 Demo stairs
File 5 Completion Installing stair treads
File 6 Power washing deck
File 7 Completion of Sainting deck and railings
File 8 Completion of staining steps
Logo, owner name, email and web site on front cover
File 9 Demo living room floor
File 10 Completion of living room floor
Please see additional on attached flyer

Target Market(s)

Residential

Industry/Entity Type

Painting

Font styles to use
Serif
Sans Serif

Requirements
Must have
• Some Photos and type of work discerption
Front page Logo, web address, phone number, owners name and email address
Back Page see attached file 1
Nice to have
• Photo maybe in middle of flyer
Use the best text that you think will meet the needs
Should not have
• No pink colors

```html
<!DOCTYPE html>
<html lang="en">
<head>
<meta charset="utf-8">
<title>TLR Handyman Service – Painting &amp; Remodeling</title>
<link href="https://fonts.googleapis.com/css2?family=Plus+Jakarta+Sans:wght@400;500;600;700;800&family=Great+Vibes&display=swap" rel="stylesheet">
<style>
  :root{
    --ink:#333333;
    --text:#3d3d3d;
    --blue:#4a5fe0;
    --blue-deep:#3b4fd1;
    --blue-light:#5f74f0;
    --gold:#c8a96e;
    --dark:#2b2b2b;
    --white:#ffffff;
  }
  *{box-sizing:border-box;margin:0;padding:0}
  html,body{width:1200px;height:927px;overflow:hidden;background:var(--white)}
  body{font-family:"Plus Jakarta Sans",sans-serif;color:var(--text);position:relative}

  .header-band{position:absolute;left:0;top:31px;width:1200px;height:64px}
  .header-band svg{position:absolute;left:0;top:0}
  .headline{position:absolute;left:26px;top:44px;font-size:29px;font-weight:400;color:var(--white);letter-spacing:-.2px;white-space:nowrap}
  .headline strong{font-weight:700}

  .brand{position:absolute;left:1062px;top:48px;width:110px;text-align:center}
  .brand-mark{display:block;width:26px;height:26px;margin:0 auto 6px;border:3px solid var(--blue)}
  .brand-name{font-size:9px;font-weight:700;color:var(--blue);line-height:1.2}

  .intro,.story{position:absolute;left:26px;width:345px;font-size:14.2px;line-height:18.2px;text-align:justify;color:var(--text)}
  .intro{top:115px}
  .story{top:749px}

  .photo{position:absolute;border-radius:3px}
  .ph-stairs{left:26px;top:233px;width:169px;height:135px;background:linear-gradient(135deg,#d9d3c6,#a89f8e)}
  .ph-floor{left:200px;top:233px;width:169px;height:135px;background:linear-gradient(160deg,#cfc6b3,#8c8a86)}
  .ph-room{left:26px;top:375px;width:343px;height:203px;background:linear-gradient(120deg,#d8d2c8,#bfb4a5 60%,#a8977f)}
  .ph-cabinet-prep{left:26px;top:587px;width:169px;height:135px;background:linear-gradient(150deg,#e6e1d8,#b9b0a2)}
  .ph-cabinet-paint{left:200px;top:587px;width:169px;height:135px;background:linear-gradient(150deg,#6b6f74,#c4b49b)}
  .ph-house{left:829px;top:401px;width:172px;height:225px;background:linear-gradient(180deg,#b9cbe0 0%,#b77a46 40%,#5f8a3a 62%,#4a7a2c)}
  .ph-deck{left:1007px;top:401px;width:171px;height:225px;background:linear-gradient(180deg,#6d7f99 0%,#e8ecef 45%,#8b4a30 80%,#6a3423)}

  .service{position:absolute}
  .service-title{height:37px;border-radius:4px;display:flex;align-items:center;justify-content:center;font-size:19px;font-weight:700;letter-spacing:2.4px;color:var(--white)}
  .t-blue{background:linear-gradient(90deg,var(--blue-deep),var(--blue-light))}
  .t-dark{background:var(--dark)}
  .t-gold{background:var(--gold);color:var(--ink)}
  .service ul{list-style:none;margin-top:13px}
  .service li{position:relative;padding-left:32px;font-size:16.4px;font-weight:500;line-height:23px;color:var(--ink);white-space:nowrap}
  .service li svg{position:absolute;left:8px;top:6px}
  .col-mid li{padding-left:36px}

  .interior{left:454px;top:114px;width:283px}
  .exterior{left:454px;top:317px;width:283px}
  .carpentry{left:454px;top:546px;width:283px}
  .maintenance{left:854px;top:114px;width:283px}
  .maintenance li{padding-left:34px}
  .maintenance li svg{left:7px}

  .mission{position:absolute;left:836px;top:655px;width:334px}
  .mission-head{display:flex;align-items:center;justify-content:center;gap:12px}
  .mission-head span{display:block;width:57px;height:2px;background:var(--dark)}
  .mission-head h2{font-family:"Great Vibes",cursive;font-weight:400;font-size:38px;color:var(--blue);line-height:46px}
  .mission p{margin-top:4px;font-size:13.6px;line-height:16px;text-align:justify;color:var(--text)}

  .contact-bar{position:absolute;left:0;top:866px;width:1200px;height:61px;display:flex}
  .contact-bar div{display:flex;align-items:center;justify-content:center;font-size:16.5px;font-weight:500}
  .c-mail{width:402px;background:var(--blue);color:var(--white)}
  .c-web{width:402px;background:var(--gold);color:var(--ink)}
  .c-call{width:396px;background:linear-gradient(90deg,var(--blue-deep),var(--blue-light));color:var(--white);font-weight:700 !important;font-size:17.5px !important}
</style>
</head>
<body>

<header class="header-band">
  <svg width="1200" height="64" viewBox="0 0 1200 64" aria-hidden="true">
    <polygon points="0,0 1004,0 976,64 0,64" fill="#333333"/>
    <polygon points="1012,0 1050,0 1022,64 984,64" fill="#c8a96e"/>
  </svg>
</header>
<h1 class="headline">Serving Southern Maine for All Your <strong>Painting and Remodeling Needs</strong></h1>

<div class="brand">
  <span class="brand-mark"></span>
  <div class="brand-name">TLR Handyman Service</div>
</div>

<p class="intro">We provide a full consultation to explain available options so that you can choose the service that’s right for your home or business. We strive to meet your project's needs and also to prevent potential problems in the future.</p>

<div class="photo ph-stairs" role="img" aria-label="Photo: stairway demolition in progress"></div>
<div class="photo ph-floor" role="img" aria-label="Photo: completed living room floor"></div>
<div class="photo ph-room" role="img" aria-label="Photo: living room covered in plastic sheeting with a ladder, prepped for painting"></div>
<div class="photo ph-cabinet-prep" role="img" aria-label="Photo: kitchen cabinets being prepped"></div>
<div class="photo ph-cabinet-paint" role="img" aria-label="Photo: freshly painted grey kitchen cabinets"></div>

<p class="story">I have always been that person who can fix anything. Repair knowledge is not enough without skills. From woodworking to electrical installation, I have fostered all of the skills you need for household repairs and improvements.</p>

<svg width="0" height="0" style="position:absolute" aria-hidden="true">
  <symbol id="tick" viewBox="0 0 12 12">
    <circle cx="6" cy="6" r="5.2" fill="none" stroke="#4a5fe0" stroke-width="1.1"/>
    <path d="M3.6 6.2 L5.4 7.9 L8.5 4.4" fill="none" stroke="#4a5fe0" stroke-width="1.2" stroke-linecap="round" stroke-linejoin="round"/>
  </symbol>
</svg>

<section class="service col-mid interior">
  <h3 class="service-title t-blue">INTERIOR PAINTING</h3>
  <ul>
    <li style="padding-left:32px"><svg width="12" height="12"><use href="#tick"/></svg>Commercial &amp; Residential</li>
    <li style="padding-left:32px"><svg width="12" height="12"><use href="#tick"/></svg>Kitchen Cabinets</li>
    <li style="padding-left:32px"><svg width="12" height="12"><use href="#tick"/></svg>Painting</li>
    <li style="padding-left:32px"><svg width="12" height="12"><use href="#tick"/></svg>Walls trim &amp; doors</li>
    <li style="padding-left:32px"><svg width="12" height="12"><use href="#tick"/></svg>Ceiling Repair</li>
    <li style="padding-left:32px"><svg width="12" height="12"><use href="#tick"/></svg>Staining &amp; polying trim</li>
  </ul>
</section>

<section class="service col-mid exterior">
  <h3 class="service-title t-dark">EXTERIOR PAINTING</h3>
  <ul>
    <li><svg width="12" height="12"><use href="#tick"/></svg>Commercial &amp; Residential</li>
    <li><svg width="12" height="12"><use href="#tick"/></svg>New Painting &amp; Updates</li>
    <li><svg width="12" height="12"><use href="#tick"/></svg>All types of Siding</li>
    <li><svg width="12" height="12"><use href="#tick"/></svg>Power washing</li>
    <li><svg width="12" height="12"><use href="#tick"/></svg>Painting &amp; Staining of decks</li>
    <li><svg width="12" height="12"><use href="#tick"/></svg>Fence cleaning painting &amp; sealing</li>
    <li><svg width="12" height="12"><use href="#tick"/></svg>Furniture cleaning, painting &amp; sealing</li>
  </ul>
</section>

<section class="service col-mid carpentry">
  <h3 class="service-title t-gold">CARPENTRY</h3>
  <ul>
    <li><svg width="12" height="12"><use href="#tick"/></svg>Commercial &amp; Residential</li>
    <li><svg width="12" height="12"><use href="#tick"/></svg>Kitchen remodeling</li>
    <li><svg width="12" height="12"><use href="#tick"/></svg>Marble &amp; Granite countertops</li>
    <li><svg width="12" height="12"><use href="#tick"/></svg>Bathroom remodeling</li>
    <li><svg width="12" height="12"><use href="#tick"/></svg>Basement remodeling</li>
    <li><svg width="12" height="12"><use href="#tick"/></svg>Disabled&nbsp; accessible ramps &amp;<br>bathroom installation</li>
    <li><svg width="12" height="12"><use href="#tick"/></svg>Room additions</li>
    <li><svg width="12" height="12"><use href="#tick"/></svg>All types of siding</li>
    <li><svg width="12" height="12"><use href="#tick"/></svg>Cabinetry</li>
    <li><svg width="12" height="12"><use href="#tick"/></svg>Sheet rocking</li>
  </ul>
</section>

<section class="service maintenance">
  <h3 class="service-title t-dark">MAINTENANCE</h3>
  <ul>
    <li><svg width="12" height="12"><use href="#tick"/></svg>Commercial &amp; Residential</li>
    <li><svg width="12" height="12"><use href="#tick"/></svg>Hanging Curtains &amp; Blinds</li>
    <li><svg width="12" height="12"><use href="#tick"/></svg>Shelving</li>
    <li><svg width="12" height="12"><use href="#tick"/></svg>Lighting</li>
    <li><svg width="12" height="12"><use href="#tick"/></svg>Picture hanging</li>
    <li><svg width="12" height="12"><use href="#tick"/></svg>TV mounting</li>
    <li><svg width="12" height="12"><use href="#tick"/></svg>Desk &amp; furniture&nbsp; assembly</li>
    <li><svg width="12" height="12"><use href="#tick"/></svg>Fixture installation&nbsp; &amp; repair</li>
    <li><svg width="12" height="12"><use href="#tick"/></svg>Clean out basement &amp; storage areas</li>
  </ul>
</section>

<div class="photo ph-house" role="img" aria-label="Photo: house exterior with lawn during siding work"></div>
<div class="photo ph-deck" role="img" aria-label="Photo: completed stained deck steps and white railings"></div>

<section class="mission">
  <div class="mission-head"><span></span><h2>The Mission</h2><span></span></div>
  <p>At TLR Handyman Service we are committed to client satisfaction and understanding that customer service is the foundation of our business. We are dedicated to providing our clients with quality workmanship performed in a prompt, professional manner. Our reliable team, second to non, will arrive neat in appearance and ready to work. Our technicians will treat each job, large or small, with the same care we would if we were repairing our own home.</p>
</section>

<footer class="contact-bar">
  <div class="c-mail">Mail us : dana@tlrhandyman.com</div>
  <div class="c-web">Visit Us : www.tlrhandyman.com</div>
  <div class="c-call">CALL US : (207) 555-0148</div>
</footer>

</body>
</html>
```